Fresh, modern, fun business card for pediatric dental practice

Need a business card for fresh, modern, fun pediatric dental practice

Clean look that matches our website's font and colors

We prefer the look of curved corners on business cards

Target Market(s)

parents (mothers) of young children, professionals, mid-high class

Industry/Entity Type

Dental

Contact Information for Business Card

Maplebrook Pediatric Dentistry
482 Quarry Lane
Suite 517
Fernwood, PA 17599
717.555.0193
www.maplebrookkidsdental.example

Mei-Ran Tsai, DMD
Corinne Walbeck, DMD
(we are working on our email address, but we would like that on the card as well)

Font styles to use
Sans Serif

Requirements
Must have
• All info; we would also like to make cards for individual staff members
• colors from our website and color palatte, attatched
• use same font and design as website for branding
Nice to have
• clean, simple card that has a pop of color
• we would like to see a few designs with our tag line "where smiles get brighter"
• we are not sure if we want to have it on there or not
• we would like to see a few designs incorporating the ribbon graphic on our website where the word WELCOME is

```html
<!DOCTYPE html>
<html lang="en">
<head>
<meta charset="utf-8">
<title>Maplebrook Pediatric Dentistry – Business Card</title>
<link rel="stylesheet" href="https://fonts.googleapis.com/css2?family=Raleway:wght@500;600&family=Lato:wght@400&display=swap">
<style>
  :root {
    --canvas-bg: #e8e5e1;
    --card-bg: #f7f7f6;
    --sun-yellow: #f8bd2a;
    --brand-orange: #f0ac1d;
    --brand-magenta: #cc1f8a;
    --ink: #3a3a3a;
    --white: #ffffff;
  }
  * { margin: 0; padding: 0; box-sizing: border-box; }
  html, body {
    width: 1200px;
    height: 900px;
    overflow: hidden;
    background: var(--canvas-bg);
  }
  .card {
    position: absolute;
    left: 145px;
    top: 170px;
    width: 910px;
    height: 560px;
    background: var(--card-bg);
    border-radius: 26px;
    overflow: hidden;
    box-shadow: 0 10px 30px rgba(0,0,0,0.12);
    font-family: "Lato", sans-serif;
  }
  .brand {
    position: absolute;
    left: 46px;
    top: 122px;
    color: var(--brand-orange);
    font-family: "Raleway", sans-serif;
    font-weight: 600;
    line-height: 1;
  }
  .brand-name { font-size: 46px; letter-spacing: 0.5px; display: block; }
  .brand-sub { font-size: 23px; letter-spacing: 1.2px; display: block; margin-top: 6px; }
  .doctors {
    position: absolute;
    right: 43px;
    top: 100px;
    text-align: right;
    font-family: "Raleway", sans-serif;
    font-weight: 500;
    font-size: 31px;
    line-height: 44px;
  }
  .doctor-primary { color: var(--brand-orange); }
  .doctor-secondary { color: var(--brand-magenta); }
  .contact-band {
    position: absolute;
    left: 0;
    top: 240px;
    width: 100%;
    height: 210px;
    background: var(--sun-yellow);
  }
  .band-disc {
    position: absolute;
    left: 25px;
    top: 223px;
    width: 258px;
    height: 258px;
    border-radius: 50%;
    background: var(--card-bg);
  }
  .contact-list {
    position: absolute;
    right: 45px;
    top: 276px;
    list-style: none;
    text-align: right;
    color: var(--white);
    font-size: 24px;
    line-height: 34px;
  }
  .contact-list li { display: flex; justify-content: flex-end; align-items: center; gap: 9px; }
  .contact-icon { width: 19px; height: 19px; fill: var(--white); flex: none; }
  .address {
    position: absolute;
    right: 52px;
    top: 482px;
    color: var(--ink);
    font-size: 25px;
    word-spacing: 1px;
  }
</style>
</head>
<body>
  <article class="card">
    <div class="brand">
      <span class="brand-name">maplebrook</span>
      <span class="brand-sub">pediatric dentistry</span>
    </div>

    <div class="doctors">
      <p class="doctor-primary">Mei-Ran Tsai, DMD</p>
      <p class="doctor-secondary">Corinne Walbeck, DMD</p>
    </div>

    <div class="contact-band"></div>
    <div class="band-disc"></div>

    <ul class="contact-list">
      <li>717.555.0193
        <svg class="contact-icon" viewBox="0 0 20 20"><path d="M3 5c0-1.5 2-3 7-3s7 1.5 7 3v2h-4V5.5H7V7H3zM5 9h10l2 8H3zM10 10.5a2.8 2.8 0 1 0 0 5.6a2.8 2.8 0 1 0 0-5.6z"/></svg>
      </li>
      <li>Mei-ran@maplebrookkidsdental.example
        <svg class="contact-icon" viewBox="0 0 20 20"><path d="M2 4h16v12H2zM3.5 5.5v.6L10 11l6.5-4.9v-.6zM3.5 8v6.5h13V8L10 12.9z"/></svg>
      </li>
      <li>Corinne@maplebrookkidsdental.example
        <svg class="contact-icon" viewBox="0 0 20 20"><path d="M2 4h16v12H2zM3.5 5.5v.6L10 11l6.5-4.9v-.6zM3.5 8v6.5h13V8L10 12.9z"/></svg>
      </li>
      <li>www.maplebrookkidsdental.example
        <svg class="contact-icon" viewBox="0 0 20 20"><path d="M10 1.5a8.5 8.5 0 1 0 0 17a8.5 8.5 0 1 0 0-17zM6 5c1.5.5 2 1.8 1.2 3S5 9.5 4.5 11C4 9 4.5 6.5 6 5zm5 2c1.5-.5 3 0 4 1.5c.5 2 0 4-1 5.5c-1-1.5-.5-3-2-3.5s-2.5-2-1-3.5zM8 13c1 .5 1.5 1.5 1 3c-1.5 0-2.5-1-3-2c.5-.8 1.2-1.2 2-1z"/></svg>
      </li>
    </ul>

    <p class="address">482 Quarry Lane&nbsp; Suite 517&nbsp; Fernwood, PA 17599</p>
  </article>
</body>
</html>
```